Business Cards Design for the electrical wholesaler: clean bold dynamic :)

We need a business card design that would follow our latest brand guidelines. As an electrical wholesaler we want to bring a fresh look and feel into the industry. The design should be clean bold and dynamic. It should come alive with the renewed energy of our green colour. Our grey colour should keep things balanced and complement the notion of maturity and responsibility. We employ Lato as a corporate font however are not bound by this font and we’re open to interpretation here.

Target Market(s)

Electrical contractors

Industry/Entity Type

Business

Contact Information for Business Card

Logo
Name & Surname: Halyna Dorosh
Job Title: Director of Marketing
Email: halya.dorosh@quillmail.example
Cell phone: XXX.XXX.XXXX
Address: 20517 - 87 Ave. Edmonton, AB, Canada. T6K 4N8
Business Phone: 780.555.0184
Website: www.brovix.example

Font styles to use
Other font styles liked:
• Lato

Requirements
Must have
• Logo & website
Nice to have
• Brand elements - some of them you may find in the attached Brand Guidelines (e.g. three lines on the background signifying "W")

```html
<!DOCTYPE html>
<html lang="en">
<head>
<meta charset="UTF-8">
<title>brovix business card</title>
<link href="https://fonts.googleapis.com/css2?family=Poppins:wght@400;500;600&display=swap" rel="stylesheet">
<style>
  :root {
    --stage: #e6e7e8;
    --brand-green: #8cc63f;
    --brand-grey: #4d4e50;
    --text-grey: #414244;
    --paper: #ffffff;
  }
  * { margin: 0; padding: 0; box-sizing: border-box; }
  html, body { width: 1200px; height: 900px; overflow: hidden; }
  body {
    background: var(--stage);
    font-family: "Poppins", sans-serif;
    position: relative;
  }
  .card {
    position: absolute;
    left: 250px;
    width: 700px;
    height: 400px;
    overflow: hidden;
    box-shadow: 0 6px 18px rgba(0,0,0,0.18);
  }
  /* Back side */
  .card-back { top: 35px; background: var(--brand-grey); }
  .card-back .brand {
    position: absolute;
    left: 0; right: 0; top: 140px;
    display: flex; justify-content: center; align-items: center; gap: 22px;
  }
  .card-back .brand-square {
    width: 56px; height: 56px; background: var(--brand-green);
  }
  .card-back .brand-name {
    font-size: 84px; font-weight: 500; color: var(--paper);
    letter-spacing: 1px; line-height: 1;
  }
  .card-back .website {
    position: absolute; left: 0; right: 0; bottom: 48px;
    text-align: center; font-size: 19px; color: var(--paper); letter-spacing: 1.5px;
  }
  .website .accent { color: var(--brand-green); }

  /* Front side */
  .card-front { top: 465px; background: var(--paper); }
  .card-front .brand {
    position: absolute; left: 42px; top: 36px;
    display: flex; align-items: center; gap: 14px;
  }
  .card-front .brand-square { width: 36px; height: 36px; background: var(--brand-green); }
  .card-front .brand-name {
    font-size: 50px; font-weight: 500; color: var(--brand-grey); line-height: 1;
  }
  .person {
    position: absolute; right: 44px; top: 50px; text-align: right;
  }
  .person-name {
    font-size: 28px; font-weight: 600; color: var(--brand-green); letter-spacing: 1px;
  }
  .person-title {
    font-size: 17px; color: var(--text-grey); letter-spacing: 1px; margin-top: 2px;
  }
  .contact {
    position: absolute; left: 56px; top: 200px;
    color: var(--text-grey); font-size: 16px; letter-spacing: 0.6px;
  }
  .contact-line { display: flex; align-items: center; gap: 12px; height: 28px; }
  .contact-line svg { width: 14px; height: 14px; flex: none; }
  .address { margin-top: 14px; line-height: 1.55; max-width: 300px; }
  .rule {
    position: absolute; left: 0; right: 0; top: 338px;
    height: 2px; background: var(--brand-green);
  }
  .base-band {
    position: absolute; left: 0; right: 0; top: 348px; bottom: 0;
    background: var(--brand-grey);
  }
  .card-front .website {
    position: absolute; right: 0; top: 318px;
    background: var(--paper); padding: 6px 44px 6px 18px;
    font-size: 19px; color: var(--text-grey); letter-spacing: 1.5px;
  }
</style>
</head>
<body>
  <section class="card card-back">
    <div class="brand">
      <span class="brand-square"></span>
      <span class="brand-name">brovix</span>
    </div>
    <p class="website">www.<span class="accent">brovix</span>.example</p>
  </section>

  <section class="card card-front">
    <div class="brand">
      <span class="brand-square"></span>
      <span class="brand-name">brovix</span>
    </div>
    <div class="person">
      <p class="person-name">Halyna Dorosh</p>
      <p class="person-title">Founder</p>
    </div>
    <div class="contact">
      <p class="contact-line">
        <svg viewBox="0 0 14 14" aria-hidden="true"><path d="M3 1 L5.5 1 L6.3 4 L4.6 5.2 Q6 8 8.8 9.4 L10 7.7 L13 8.5 L13 11 Q12 13 10 13 Q2 11.5 1 4 Q1 2 3 1 Z" fill="var(--brand-green)"/></svg>
        <span>780.555.0184</span>
      </p>
      <p class="contact-line">
        <svg viewBox="0 0 14 14" aria-hidden="true"><rect x="1" y="3" width="12" height="8.5" rx="1" fill="none" stroke="var(--brand-green)" stroke-width="1.4"/><path d="M1.5 3.5 L7 8 L12.5 3.5" fill="none" stroke="var(--brand-green)" stroke-width="1.4"/></svg>
        <span>halya.dorosh@quillmail.example</span>
      </p>
      <p class="address">20517 - 87 Ave. Edmonton, AB, Canada. T6K 4N8</p>
    </div>
    <div class="rule"></div>
    <div class="base-band"></div>
    <p class="website">www.<span class="accent">brovix</span>.example</p>
  </section>
</body>
</html>
```